Design Website Templates for Photographers for Lumera Inc. (trylumera.example)

Lumera Inc. is a generative website company for wedding photographers.
We are seeking new photography website design inspirations for the next template to be offered on our platform. The catch is you must use the same data for your designs. You also must use all of the data somewhere in the design. You cannot add new content besides the data available. If you wish to add any elements It will be hardcoded and must be universally fitting for many different photographers. We recommend not using any hardcoded test.
Don't be afraid to be creative! Although the most important element of a photographers website is the photos, we are looking for unique and out-of-the-box designs for the actual site as well.
Here is the User generated data available to you:
- 4 Hero Images Landscape, 4 Hero Images Portrait
- Tagline “destination photographer based in Maui, Hawaii”
- “About Photo” of the photographer
- “About” Biography Text
- The design can use up to 3 colors + background color and 2 fonts
- 9 Gallery images
- 3 Packages/services that include landscape/portrait images, a price, a title and text
- Testimonials made up of an image, text and text for the name of testimonial giver
See some examples of our current website designs attached. You can use any of the data you see in the designs.
Updates
We are looking for designs that are less feminine and are more neutral in color and fonts. Currently our templates are more oriented towards feminine photographers. We want to have designs that speak to diverse audiences. We thank everyone for submitting and are reviewing the designs.
Number of Pages Required
1 page
Look and feel
Each slider illustrates characteristics of the customer's brand and the style your logo design should communicate.

```html
<!DOCTYPE html>
<html lang="en">
<head>
<meta charset="utf-8">
<title>Lumera — Destination Photographer</title>
<link href="https://fonts.googleapis.com/css2?family=IBM+Plex+Sans:wght@300;400;500;600&family=Lora:wght@400;600;700&display=swap" rel="stylesheet">
<style>
:root{
  --accent:#f07f2a;
  --ink:#2b2b2b;
  --body:#555555;
  --paper:#ffffff;
  --mist:#efeeec;
  --night:#1e1e1e;
  --line:#d6d6d6;
}
*{box-sizing:border-box;margin:0;padding:0}
html,body{width:1200px;height:4946px;overflow:hidden;background:var(--paper)}
body{position:relative;font-family:"Lora",serif;color:var(--ink)}
.abs{position:absolute}
.sans{font-family:"IBM Plex Sans",sans-serif}

/* nav */
.brand{font-family:"IBM Plex Sans",sans-serif;font-weight:600;font-size:34px;letter-spacing:2px;color:var(--accent);line-height:1}
.nav{display:flex;align-items:center;font-family:"IBM Plex Sans",sans-serif;font-size:14px;color:var(--paper)}
.nav a{color:inherit;text-decoration:none;margin-right:46px;text-transform:uppercase}
.nav a.active{background:var(--accent);padding:8px 12px;margin-right:28px}
.nav a:last-child{margin-right:0}

/* hero */
.hero{left:0;top:0;width:1200px;height:668px;
  background:
    radial-gradient(ellipse 220px 300px at 560px 360px,rgba(250,245,240,.75),rgba(250,245,240,0) 70%),
    radial-gradient(ellipse 200px 320px at 720px 470px,rgba(90,92,100,.8),rgba(90,92,100,0) 75%),
    radial-gradient(ellipse 160px 120px at 600px 500px,rgba(200,120,70,.6),rgba(200,120,70,0) 75%),
    radial-gradient(ellipse 260px 340px at 1120px 300px,rgba(214,160,60,.7),rgba(214,160,60,0) 75%),
    radial-gradient(ellipse 420px 260px at 180px 140px,rgba(235,225,210,.5),rgba(235,225,210,0) 75%),
    linear-gradient(180deg,rgba(0,0,0,0) 55%,rgba(40,30,20,.35) 100%),
    linear-gradient(100deg,#7f6a55 0%,#a8927a 28%,#c8b8a2 48%,#9c8870 68%,#b29560 88%,#8a6f40 100%)}
.hero-title{left:127px;top:212px;width:360px;font-family:"Lora",serif;font-weight:700;font-size:47px;line-height:51px;color:var(--paper);text-shadow:0 1px 6px rgba(0,0,0,.25)}
.circle-btn{width:24px;height:24px;border:1.5px solid currentColor;border-radius:50%;display:flex;align-items:center;justify-content:center}

/* headings */
.h2{font-family:"IBM Plex Sans",sans-serif;font-weight:400;font-size:31px;color:var(--ink);text-transform:uppercase;letter-spacing:.5px}
.h2.center{width:1200px;left:0;text-align:center}
.rule{height:2px;width:44px;background:var(--ink)}
.copy{font-family:"Lora",serif;font-size:14.3px;line-height:22.4px;color:var(--body)}

.band{left:0;width:1200px;background:var(--mist)}

/* photo tiles */
.shot{overflow:hidden}

/* packages */
.card{background:var(--paper);text-align:center}
.card h3{font-family:"IBM Plex Sans",sans-serif;font-weight:400;font-size:19px;margin-top:30px;color:var(--ink)}
.card p{font-family:"Lora",serif;font-size:12.2px;line-height:15.5px;color:var(--body);width:240px;margin:8px auto 0}
.card .price{font-family:"IBM Plex Sans",sans-serif;font-weight:600;font-size:20px;color:var(--accent);margin-top:14px}

/* testimonials */
.quote-card{border:2px solid var(--line);background:var(--paper);text-align:center}
.quote-card .mark{font-family:"Lora",serif;font-style:italic;font-size:42px;color:var(--ink);line-height:1;margin-top:68px}
.quote-card p{font-family:"Lora",serif;font-size:12.8px;line-height:17.6px;color:var(--body);width:240px;margin:10px auto 0}
.quote-card .dash{width:36px;height:1px;background:#999;margin:26px auto 0}
.quote-card .who{font-family:"Lora",serif;font-size:12.8px;color:var(--body);margin-top:16px}
.avatar{width:86px;height:86px;border-radius:50%;border:2px solid var(--paper)}

/* form */
.field{background:var(--paper);font-family:"Lora",serif;font-size:12.5px;color:#666;padding:14px 20px}
.submit{background:var(--accent);color:var(--paper);font-family:"IBM Plex Sans",sans-serif;font-weight:500;font-size:18px;letter-spacing:.5px;display:flex;align-items:center;justify-content:center}

/* footer */
.footer{left:0;top:4754px;width:1200px;height:192px;background:var(--night)}
</style>
</head>
<body>

<!-- HERO -->
<section class="abs hero" role="img" aria-label="Hero photograph of a smiling bride and groom in front of a sunlit rock wall"></section>
<div class="abs brand" style="left:129px;top:24px">LUMERA</div>
<nav class="abs nav" style="left:480px;top:24px">
  <a class="active">Home</a><a>About</a><a>Blog</a><a>Testimonials</a><a>Portfolio</a><a>Get in touch</a>
</nav>
<h1 class="abs hero-title">Destination photographer based in Maui, Hawaii</h1>
<div class="abs circle-btn" style="left:136px;top:547px;color:#fff">
  <svg width="10" height="10" viewBox="0 0 10 10"><path d="M6.5 1.5 3 5l3.5 3.5" fill="none" stroke="#fff" stroke-width="1.5"/></svg>
</div>
<div class="abs circle-btn" style="left:176px;top:547px;color:#fff">
  <svg width="10" height="10" viewBox="0 0 10 10"><path d="M3.5 1.5 7 5 3.5 8.5" fill="none" stroke="#fff" stroke-width="1.5"/></svg>
</div>

<!-- ABOUT ME -->
<h2 class="abs h2" style="left:134px;top:727px">About Me</h2>
<div class="abs rule" style="left:134px;top:777px;width:100px"></div>
<div class="abs copy" style="left:134px;top:806px;width:440px">
  <p>Sed ut perspiciatis unde omnis iste natus error sit voluptatem accusantium doloremque laudantium, totam rem aperiam, eaque ipsa quae ab illo inventore veritatis et quasi architecto beatae vitae dicta sunt explicabo. Nemo enim ipsam voluptatem quia voluptas sit aspernatur aut odit aut fugit, sed quia consequuntur magni dolores eos qui ratione voluptatem sequi nesciunt. Neque porro quisquam est, qui dolorem ipsum quia dolor sit amet, consectetur, adipisci velit, sed quia non numquam eius modi tempora incidunt.</p>
  <p style="margin-top:26px">Nemo enim ipsam voluptatem quia voluptas sit aspernatur aut odit aut fugit, sed quia consequuntur magni dolores eos qui ratione voluptatem sequi nesciunt. Neque porro quisquam est, qui dolorem ipsum quia dolor sit amet, consectetur, adipisci velit, sed quia non numquam eius modi tempora incidunt.</p>
</div>
<div class="abs shot" style="left:618px;top:720px;width:450px;height:465px;background:
  radial-gradient(ellipse 120px 240px at 230px 330px,rgba(25,25,28,.95),rgba(25,25,28,0) 80%),
  radial-gradient(ellipse 60px 70px at 200px 110px,rgba(200,160,130,.8),rgba(200,160,130,0) 80%),
  radial-gradient(ellipse 70px 160px at 80px 330px,rgba(170,180,190,.8),rgba(170,180,190,0) 80%),
  linear-gradient(90deg,#e4e4e2 0%,#d2d2d0 60%,#a8a6a2 82%,#5a544e 100%)" role="img" aria-label="Portrait of the photographer holding a camera on a staircase"></div>

<!-- ABOUT PHOTO -->
<section class="abs band" style="top:1237px;height:602px"></section>
<h2 class="abs h2 center" style="top:1282px">About Photo</h2>
<div class="abs rule" style="left:578px;top:1340px"></div>
<div class="abs shot" style="left:132px;top:1388px;width:480px;height:396px;background:
  radial-gradient(circle 40px at 160px 70px,rgba(255,230,180,.9),rgba(255,230,180,0) 80%),
  radial-gradient(circle 36px at 300px 60px,rgba(255,230,180,.85),rgba(255,230,180,0) 80%),
  radial-gradient(circle 34px at 420px 120px,rgba(255,230,180,.8),rgba(255,230,180,0) 80%),
  radial-gradient(circle 30px at 60px 160px,rgba(255,230,180,.7),rgba(255,230,180,0) 80%),
  radial-gradient(ellipse 120px 170px at 250px 300px,rgba(230,215,200,.75),rgba(230,215,200,0) 80%),
  radial-gradient(ellipse 260px 120px at 240px 360px,rgba(120,85,65,.8),rgba(120,85,65,0) 80%),
  linear-gradient(180deg,#141a33 0%,#1e2444 50%,#3c3240 100%)" role="img" aria-label="Couple kissing at night surrounded by guests holding sparklers"></div>
<p class="abs copy" style="left:662px;top:1392px;width:400px">Sed ut perspiciatis unde omnis iste natus error sit voluptatem accusantium doloremque laudantium, totam rem aperiam, eaque ipsa quae ab illo inventore veritatis et quasi architecto beatae vitae dicta sunt explicabo. Nemo enim ipsam voluptatem quia voluptas sit aspe rnatur aut odit aut fugit, sed quia consequuntur magni dolores eos qui ratione voluptatem sequi nesciunt. Neque porro quisquam est, qui dolorem ipsum quia dolor sit amet, consectetur, adipisci velit, sed quia non numquam eius modi tempora incidunt. id quod maxime placeat facere possimus, omnis voluptas assumenda est, omnis dolor repellendus. Temporibus autem quibusdam et aut officiis debitis aut rerum necessitatibus saepe eveniet ut et voluptates repudiandae sint et molestiae non recusandae. Itaque earum rerum hic tenetur a sapiente delectus, ut aut reiciendis voluptatibus maiores alias consequatur aut perferendis doloribus.</p>

<!-- GALLERY -->
<h2 class="abs h2 center" style="top:1881px">Gallery</h2>
<div class="abs rule" style="left:578px;top:1940px"></div>
<div class="abs shot" style="left:132px;top:1978px;width:300px;height:286px;background:
  radial-gradient(ellipse 70px 120px at 170px 180px,rgba(235,235,230,.9),rgba(235,235,230,0) 80%),
  radial-gradient(ellipse 90px 80px at 60px 250px,rgba(200,200,200,.6),rgba(200,200,200,0) 80%),
  linear-gradient(160deg,#1e2a1e,#3e4a36 50%,#5a5a50)" role="img" aria-label="Gallery image: couple under a floral canopy"></div>
<div class="abs shot" style="left:449px;top:1978px;width:302px;height:286px;background:
  radial-gradient(ellipse 140px 30px at 150px 20px,rgba(240,238,232,.9),rgba(240,238,232,0) 80%),
  radial-gradient(ellipse 50px 110px at 150px 170px,rgba(240,236,228,.85),rgba(240,236,228,0) 80%),
  linear-gradient(180deg,#4e6e7a 0%,#7e8e80 40%,#b89a72 70%,#d2b690 100%)" role="img" aria-label="Gallery image: couple on a beach under a draped arch"></div>
<div class="abs shot" style="left:768px;top:1978px;width:300px;height:286px;background:
  radial-gradient(ellipse 180px 120px at 150px 220px,rgba(235,238,240,.95),rgba(235,238,240,0) 80%),
  radial-gradient(ellipse 60px 60px at 130px 60px,rgba(40,40,45,.7),rgba(40,40,45,0) 80%),
  linear-gradient(160deg,#3a4850,#7e8a90 60%,#bfc4c6)" role="img" aria-label="Gallery image: couple kissing in white smoke"></div>
<div class="abs shot" style="left:132px;top:2279px;width:300px;height:286px;background:
  radial-gradient(circle 130px at 150px 150px,rgba(255,255,255,0) 70%,rgba(210,190,140,.7) 74%,rgba(255,255,255,0) 80%),
  radial-gradient(ellipse 40px 100px at 195px 190px,rgba(30,34,48,.85),rgba(30,34,48,0) 80%),
  linear-gradient(180deg,#e6e0d4,#f2eee8)" role="img" aria-label="Gallery image: couple at a round floral arch"></div>
<div class="abs shot" style="left:449px;top:2279px;width:302px;height:286px;background:
  radial-gradient(ellipse 70px 120px at 150px 170px,rgba(245,242,236,.85),rgba(245,242,236,0) 80%),
  radial-gradient(ellipse 40px 90px at 170px 130px,rgba(30,30,35,.7),rgba(30,30,35,0) 80%),
  linear-gradient(180deg,#a8a08e 0%,#8a7e62 45%,#6a5e44 100%)" role="img" aria-label="Gallery image: couple embracing in a grassy landscape"></div>
<div class="abs shot" style="left:768px;top:2279px;width:300px;height:286px;background:
  radial-gradient(ellipse 70px 120px at 200px 200px,rgba(240,236,230,.85),rgba(240,236,230,0) 80%),
  radial-gradient(ellipse 50px 120px at 100px 180px,rgba(40,60,110,.8),rgba(40,60,110,0) 80%),
  linear-gradient(180deg,#7a5a40 0%,#4a3a30 50%,#2a2a34 100%)" role="img" aria-label="Gallery image: couple walking out of a wooden chapel"></div>
<div class="abs shot" style="left:132px;top:2579px;width:300px;height:288px;background:
  radial-gradient(ellipse 90px 150px at 150px 130px,rgba(240,210,160,.7),rgba(240,210,160,0) 80%),
  radial-gradient(ellipse 60px 100px at 120px 140px,rgba(90,60,40,.6),rgba(90,60,40,0) 80%),
  linear-gradient(160deg,#d8a866,#a47040 55%,#5e4024)" role="img" aria-label="Gallery image: couple under a veil at golden hour"></div>
<div class="abs shot" style="left:449px;top:2579px;width:302px;height:288px;background:
  radial-gradient(ellipse 110px 70px at 150px 240px,rgba(240,236,232,.85),rgba(240,236,232,0) 80%),
  radial-gradient(ellipse 50px 110px at 140px 120px,rgba(60,90,80,.8),rgba(60,90,80,0) 80%),
  linear-gradient(160deg,#262a34,#4a4a52 55%,#8a827a)" role="img" aria-label="Gallery image: groom dipping bride on the dance floor"></div>
<div class="abs shot" style="left:768px;top:2579px;width:300px;height:288px;background:
  radial-gradient(circle 80px at 150px 120px,rgba(255,236,170,.95),rgba(255,236,170,0) 80%),
  radial-gradient(ellipse 50px 110px at 140px 190px,rgba(40,40,40,.6),rgba(40,40,40,0) 80%),
  linear-gradient(180deg,#9aa6ae 0%,#d8c48a 45%,#5a6030 75%,#2e3620 100%)" role="img" aria-label="Gallery image: couple kissing at sunset in a field"></div>

<!-- PACKAGES -->
<section class="abs band" style="top:2915px;height:743px"></section>
<h2 class="abs h2 center" style="top:2952px">Packages</h2>
<div class="abs card" style="left:132px;top:3039px;width:300px;height:576px">
  <div style="height:388px;background:
    radial-gradient(ellipse 60px 110px at 160px 250px,rgba(240,236,230,.85),rgba(240,236,230,0) 80%),
    radial-gradient(ellipse 140px 120px at 150px 110px,rgba(150,140,130,.7),rgba(150,140,130,0) 80%),
    linear-gradient(180deg,#c4b898 0%,#8e8470 45%,#5c5444 75%,#3e3830 100%)" role="img" aria-label="Package image: couple on a terrace by an old chapel"></div>
  <h3>PACKAGE 1</h3>
  <p>Sed ut perspiciatis unde omnis iste natus error sit voluptatem accusantium doloremque laudantium, totam rem aperiam, eaque ipsa quae ab illo inventore veritatis et.</p>
  <div class="price">$15.99</div>
</div>
<div class="abs card" style="left:450px;top:3039px;width:300px;height:576px">
  <div style="height:388px;background:
    radial-gradient(ellipse 140px 50px at 150px 80px,rgba(200,50,70,.7),rgba(200,50,70,0) 80%),
    linear-gradient(180deg,#e8e4e0 0%,#c8d0d4 22%,#5a7a80 34%,#d6d4d0 42%,#dcdad6 70%,#8a8678 85%,#5a5648 100%)" role="img" aria-label="Package image: outdoor ceremony and couple walking in hills"></div>
  <h3>PACKAGE 2</h3>
  <p>Sed ut perspiciatis unde omnis iste natus error sit voluptatem accusantium doloremque laudantium, totam rem aperiam, eaque ipsa quae ab illo inventore veritatis et.</p>
  <div class="price">$15.99</div>
</div>
<div class="abs card" style="left:768px;top:3039px;width:300px;height:576px">
  <div style="height:388px;background:
    radial-gradient(ellipse 110px 140px at 150px 290px,rgba(248,248,246,.95),rgba(248,248,246,0) 80%),
    radial-gradient(ellipse 60px 200px at 270px 220px,rgba(50,80,40,.8),rgba(50,80,40,0) 80%),
    linear-gradient(90deg,#8a7a62 0%,#b6a890 40%,#9a8c76 70%,#4a5a38 100%)" role="img" aria-label="Package image: couple embracing beside stone columns"></div>
  <h3>PACKAGE 3</h3>
  <p>Sed ut perspiciatis unde omnis iste natus error sit voluptatem accusantium doloremque laudantium, totam rem aperiam, eaque ipsa quae ab illo inventore veritatis et.</p>
  <div class="price">$15.99</div>
</div>

<!-- TESTIMONIALS -->
<h2 class="abs h2 center" style="top:3705px">Testimonials</h2>
<div class="abs rule" style="left:578px;top:3762px"></div>
<div class="abs circle-btn" style="left:73px;top:3990px;color:#333">
  <svg width="10" height="10" viewBox="0 0 10 10"><path d="M6.5 1.5 3 5l3.5 3.5" fill="none" stroke="#333" stroke-width="1.5"/></svg>
</div>
<div class="abs circle-btn" style="left:1104px;top:3990px;color:#333">
  <svg width="10" height="10" viewBox="0 0 10 10"><path d="M3.5 1.5 7 5 3.5 8.5" fill="none" stroke="#333" stroke-width="1.5"/></svg>
</div>

<div class="abs quote-card" style="left:132px;top:3830px;width:300px;height:365px">
  <div class="mark">“</div>
  <p>On the other hand, we denounce with righteous indignation and dislike men who are so beguiled and demoralized by the charms of pleasure of the moment, so blinded by desire, that they cannot foresee the pain and trouble that are bound to ensue; and equal blame belon gs to those who fail in their duty through weakness of will, which is the same as saying through.</p>
  <div class="dash"></div>
  <div class="who">Smith, US</div>
</div>
<div class="abs quote-card" style="left:450px;top:3830px;width:300px;height:365px">
  <div class="mark">“</div>
  <p>On the other hand, we denounce with righteous indignation and dislike men who are so beguiled and demoralized by the charms of pleasure of the moment, so blinded by desire, that they cannot foresee the pain and trouble that are bound to ensue; and equal blame belon gs to those who fail in their duty through weakness of will, which is the same as saying through.</p>
  <div class="dash"></div>
  <div class="who">Smith, US</div>
</div>
<div class="abs quote-card" style="left:768px;top:3830px;width:300px;height:365px">
  <div class="mark">“</div>
  <p>On the other hand, we denounce with righteous indignation and dislike men who are so beguiled and demoralized by the charms of pleasure of the moment, so blinded by desire, that they cannot foresee the pain and trouble that are bound to ensue; and equal blame belon gs to those who fail in their duty through weakness of will, which is the same as saying through.</p>
  <div class="dash"></div>
  <div class="who">Smith, US</div>
</div>
<div class="abs avatar" style="left:239px;top:3793px;background:radial-gradient(circle 40px at 50% 90%,#2a2e38,rgba(42,46,56,0) 90%),linear-gradient(180deg,#7a8a6a,#5e6a50)" role="img" aria-label="Client portrait"></div>
<div class="abs avatar" style="left:557px;top:3793px;background:radial-gradient(circle 40px at 50% 90%,#3a3430,rgba(58,52,48,0) 90%),linear-gradient(180deg,#c8beb4,#8a7e72)" role="img" aria-label="Client portrait"></div>
<div class="abs avatar" style="left:875px;top:3793px;background:radial-gradient(circle 40px at 50% 90%,#1e2024,rgba(30,32,36,0) 90%),linear-gradient(180deg,#4a5058,#2e3238)" role="img" aria-label="Client portrait"></div>

<!-- CONNECT -->
<section class="abs band" style="top:4249px;height:505px"></section>
<h2 class="abs h2 center" style="top:4287px">Lets Connect</h2>
<div class="abs field" style="left:238px;top:4378px;width:359px;height:45px">First Name</div>
<div class="abs field" style="left:613px;top:4378px;width:360px;height:45px">Last Name</div>
<div class="abs field" style="left:238px;top:4438px;width:359px;height:45px">Email id</div>
<div class="abs field" style="left:613px;top:4438px;width:360px;height:45px">Phone</div>
<div class="abs field" style="left:238px;top:4499px;width:735px;height:138px">Message</div>
<div class="abs submit" style="left:540px;top:4666px;width:120px;height:44px">SUBMIT</div>

<!-- FOOTER -->
<footer class="abs footer"></footer>
<div class="abs brand" style="left:132px;top:4794px">LUMERA</div>
<nav class="abs nav" style="left:490px;top:4800px;font-size:14px">
  <a style="margin-right:34px">Home</a><a style="margin-right:34px">About</a><a style="margin-right:34px">Blog</a><a style="margin-right:34px">Testimonials</a><a style="margin-right:34px">Portfolio</a><a>Get in touch</a>
</nav>
<div class="abs" style="left:132px;top:4852px;width:936px;height:1px;background:#3a3a3a"></div>
<div class="abs sans" style="left:0;top:4884px;width:1200px;text-align:center;font-size:12px;color:#ddd">Copyright © 2023 All Rights Reserved</div>

</body>
</html>
```